Global investment holding company - Business Card Design

Velto Range is a recently incorporated investment holding company. Based in Singapore, it has operations in global emerging markets in the transport & logistics, energy and livestock industries.

Its tagline "Collaboration for Growth" reflects the company's philosophy of helping countries progress through partnerships which generate employment and share benefits with its society.

We are looking for a business card that reflects our global presence - incorporating the logo design into the business card design. It must have a sophisticated, modern & corporate feel.

Target Market(s)

Investors and high level governmental officials

Industry/Entity Type

Investment

Requirements
Must have
• - Use of shades of blue in logo

-Profile picture

- Name: Dennis Orbeck
- Title: Chairman
- Email: dennis@veltorange-mail.com
- Mob: +65 9154 0826
- Tel: +65 6418 5092
- DID: + 65 6418 5093
- Address: 47 Harrow Lane, #08-03, Singapore 071286

- website: www.veltorange-mail.com

```html
<!DOCTYPE html>
<html lang="en">
<head>
<meta charset="utf-8">
<title>Velto Range – Business Card</title>
<link href="https://fonts.googleapis.com/css2?family=Open+Sans:wght@400;600;700&display=swap" rel="stylesheet">
<style>
  :root {
    --backdrop: #4a4a4c;
    --card: #ffffff;
    --navy: #1d4a8c;
    --sky: #7fbfe3;
    --grey-text: #4d4f53;
    --link-blue: #1f3f94;
    --photo-top: #8f9bab;
    --photo-bottom: #3e4654;
  }
  * { box-sizing: border-box; margin: 0; padding: 0; }
  html, body {
    width: 1200px; height: 534px; overflow: hidden;
    background: var(--backdrop);
    font-family: "Open Sans", Arial, sans-serif;
  }
  .canvas { position: relative; width: 1200px; height: 534px; }

  .card {
    position: absolute; top: 119px;
    width: 517px; height: 295px;
    background: var(--card);
    border-radius: 22px;
    overflow: hidden;
  }
  .card--front { left: 62px; }
  .card--back  { left: 620px; }

  /* brand lockup */
  .brand { position: absolute; display: flex; align-items: center; }
  .brand__dot { flex: none; border-radius: 50%; background: var(--sky); }
  .brand__name {
    font-weight: 700; color: var(--navy);
    text-transform: uppercase; line-height: 1.0;
  }
  .tagline {
    position: absolute; color: var(--grey-text);
    text-transform: uppercase; letter-spacing: 1.2px; white-space: nowrap;
  }

  /* front */
  .card--front .brand { left: 0; right: 0; top: 82px; justify-content: center; gap: 16px; }
  .card--front .brand__dot { width: 88px; height: 88px; }
  .card--front .brand__name { font-size: 40px; width: 150px; }
  .card--front .tagline { left: 0; right: 0; top: 190px; text-align: center; font-size: 17px; }
  .front__web {
    position: absolute; left: 0; right: 0; top: 228px;
    text-align: center; font-size: 11px; letter-spacing: 4px; color: var(--grey-text);
  }

  /* back */
  .photo {
    position: absolute; left: 48px; top: 51px; width: 118px; height: 140px;
    background: linear-gradient(180deg, var(--photo-top), var(--photo-bottom));
    border: 4px solid #fff;
    box-shadow: 0 2px 6px rgba(0,0,0,0.45);
    z-index: 2;
  }
  .card--back .brand { left: 186px; top: 60px; gap: 14px; }
  .card--back .brand__dot { width: 70px; height: 70px; }
  .card--back .brand__name { font-size: 31px; width: 120px; }
  .card--back .tagline { left: 190px; top: 146px; font-size: 13px; }

  .name-band {
    position: absolute; left: 0; right: 0; top: 173px; height: 40px;
    background: var(--navy);
    display: flex; align-items: center; padding-left: 193px;
    color: #fff;
  }
  .name-band__name { font-size: 17px; font-weight: 600; letter-spacing: 0.3px; }
  .name-band__title {
    font-size: 11px; letter-spacing: 0.5px; text-transform: uppercase;
    margin-left: 8px; padding-left: 7px; border-left: 1px solid rgba(255,255,255,0.7);
  }

  .contact {
    position: absolute; left: 0; right: 0; top: 227px;
    text-align: center; color: var(--grey-text); font-size: 12px; line-height: 18px;
    padding-left: 16px;
  }
  .contact__address { color: var(--link-blue); font-size: 13.5px; margin-bottom: 1px; }
  .contact__value { color: var(--link-blue); }
  .contact__sep { color: #9a9a9a; margin: 0 5px; }
</style>
</head>
<body>
<div class="canvas">

  <section class="card card--front" aria-label="Business card front">
    <div class="brand">
      <span class="brand__dot"></span>
      <span class="brand__name">Velto Range</span>
    </div>
    <p class="tagline">Collaboration for Growth</p>
    <p class="front__web">www.veltorange-mail.com</p>
  </section>

  <section class="card card--back" aria-label="Business card back">
    <div class="photo" role="img" aria-label="Portrait photo of Dennis Orbeck"></div>
    <div class="brand">
      <span class="brand__dot"></span>
      <span class="brand__name">Velto Range</span>
    </div>
    <p class="tagline">Collaboration for Growth</p>

    <div class="name-band">
      <span class="name-band__name">DENNIS ORBECK</span>
      <span class="name-band__title">Chairman</span>
    </div>

    <div class="contact">
      <p class="contact__address">47 Harrow Lane, #08-03, Singapore 071286</p>
      <p>mobile: <span class="contact__value">+65 9154 0826</span><span class="contact__sep">|</span>tel: <span class="contact__value">+65 6418 5092</span><span class="contact__sep">|</span>did: <span class="contact__value">+ 65 6418 5093</span></p>
      <p>email: <span class="contact__value">dennis@veltorange-mail.com</span><span class="contact__sep">|</span>web: <span class="contact__value">www.veltorange-mail.com</span></p>
    </div>
  </section>

</div>
</body>
</html>
```